Folder Design: Mobile Laboratory Service

Need a folder designed for a Mobile Laboratory Service. Folder needs to be very professional and will be used to hold brochure, contract and business card of business. Logos of the company are attached.

Industry/Entity Type

Healthcare

```html
<!DOCTYPE html>
<html lang="en">
<head>
<meta charset="utf-8">
<title>Meridian Mobile Labs – Presentation Folder</title>
<link rel="stylesheet" href="https://fonts.googleapis.com/css2?family=Jost:wght@500;600;700&family=Poppins:wght@400;500&display=swap">
<style>
:root{
  --page:#ffffff;
  --board:#d4d4d4;
  --navy-deep:#111823;
  --navy:#1b2233;
  --navy-light:#252e45;
  --wave:#2a3350;
  --blue:#5b9be0;
  --blue-line:#2f6ec8;
  --white:#ffffff;
  --ink:#121826;
  --dash:#5a5a5a;
}
*{margin:0;padding:0;box-sizing:border-box}
html,body{width:1200px;height:2183px;overflow:hidden;background:var(--page)}
body{position:relative;font-family:'Poppins',sans-serif}
.board{position:absolute;left:40px;width:1120px;height:1007px;background:var(--board)}
.board--outside{top:51px}
.board--inside{top:1131px}
.abs{position:absolute}
.center{transform:translateX(-50%);text-align:center;white-space:nowrap}
.headline{font-family:'Jost',sans-serif;font-weight:700;text-transform:uppercase}
.brand-mark{position:absolute;transform:translate(-50%,-50%);display:flex;flex-direction:column;align-items:center;gap:8px}
.brand-mark__circle{border:3px solid var(--blue);border-radius:50%}
.brand-mark__name{font-family:'Jost',sans-serif;font-weight:600;color:var(--blue);font-size:15px;white-space:nowrap}
.contact{position:absolute;left:417px;font-size:10.5px;color:var(--ink);line-height:14px}
.contact-icon{position:absolute;left:390px}
.intro{position:absolute;left:139px;top:1552px;width:397px;font-size:7.7px;line-height:11.6px;color:var(--white);text-align:justify;text-align-last:left}
.services{position:absolute;left:139px;top:1630px;width:397px;height:116px;border:1.5px solid var(--blue-line);border-radius:10px}
.service{position:absolute;font-size:10.5px;color:var(--white);display:flex;align-items:center;gap:7px}
</style>
</head>
<body>

<!-- Outside spread -->
<div class="board board--outside"></div>
<svg class="abs" style="left:0;top:0" width="1200" height="1060" viewBox="0 0 1200 1060">
  <defs>
    <linearGradient id="coverBg" x1="0" y1="0" x2="0" y2="1">
      <stop offset="0" stop-color="#111823"/><stop offset="1" stop-color="#161d2b"/>
    </linearGradient>
  </defs>
  <rect x="124" y="102" width="986" height="509" fill="url(#coverBg)"/>
  <path d="M505 102 C600 140 610 300 720 330 C860 370 1000 330 1110 465 L1110 102 Z" fill="#1d2539"/>
  <path d="M505 102 C590 150 600 270 700 300 C840 340 990 310 1110 440 L1110 465 C1000 330 860 370 720 330 C610 300 600 140 505 102Z" fill="#0d131d"/>
  <path d="M124 102 L505 102 C580 160 590 250 560 320 L124 611 Z" fill="#1f2637" opacity=".55"/>
  <rect x="124" y="611" width="986" height="173" fill="#ffffff"/>
  <polygon points="92,795 124,784 611,784 579,1008 124,1008 92,997" fill="#ffffff" stroke="#9a9a9a" stroke-width="1"/>
  <line x1="617" y1="102" x2="617" y2="784" stroke="var(--dash)" stroke-dasharray="5 4"/>
  <line x1="124" y1="784" x2="611" y2="784" stroke="var(--dash)" stroke-dasharray="5 4"/>
  <line x1="124" y1="784" x2="124" y2="1008" stroke="var(--dash)" stroke-dasharray="5 4"/>
  <rect x="261" y="835" width="213" height="123" rx="8" fill="none" stroke="var(--blue-line)" stroke-width="1.2"/>
  <line x1="254" y1="860" x2="289" y2="829" stroke="var(--blue-line)"/>
  <line x1="447" y1="967" x2="482" y2="935" stroke="var(--blue-line)"/>
  <circle cx="370" cy="332" r="161" fill="none" stroke="#2f7fd4" stroke-width="2.5"/>
  <circle cx="370" cy="332" r="148" fill="#5e9ed8" role="img" aria-label="Photo of a lab scientist looking through a microscope"/>
  <line x1="370" y1="632" x2="370" y2="760" stroke="var(--blue-line)" stroke-width="1.2"/>
</svg>

<div class="abs center headline" style="left:370px;top:518px;font-size:20.5px;line-height:23px;color:var(--white);font-weight:600">Laboratory results that<br>you can trust</div>
<div class="abs center headline" style="left:863px;top:156px;font-size:15.5px;color:var(--white);font-weight:600">Meridian Mobile Labs</div>
<div class="abs center headline" style="left:863px;top:206px;font-size:19.5px;color:var(--blue);font-weight:600">Cutting-edge pathology lab</div>
<div class="abs center headline" style="left:863px;top:232px;font-size:50px;line-height:56px;color:var(--blue)">Diagnosing<br>the future</div>

<div class="brand-mark" style="left:861px;top:488px">
  <div class="brand-mark__circle" style="width:116px;height:116px"></div>
  <div class="brand-mark__name">Meridian Mobile Labs</div>
</div>

<div class="brand-mark" style="left:249px;top:700px">
  <div class="brand-mark__circle" style="width:88px;height:88px"></div>
  <div class="brand-mark__name" style="font-size:13px">Meridian Mobile Labs</div>
</div>

<svg class="contact-icon" style="top:634px" width="18" height="18" viewBox="0 0 18 18"><circle cx="9" cy="9" r="8" fill="none" stroke="#2f5fa8" stroke-width="1.2"/><path d="M6 5.5l1.6-.3.9 2-1 .8a5 5 0 0 0 2.5 2.5l.8-1 2 .9-.3 1.6c-3.5.3-6.8-3-6.5-6.5z" fill="#2f5fa8"/></svg>
<div class="contact" style="top:636px">(555) 013-4821</div>
<svg class="contact-icon" style="top:666px" width="18" height="18" viewBox="0 0 18 18"><circle cx="9" cy="9" r="8" fill="none" stroke="#2f5fa8" stroke-width="1.2"/><rect x="5" y="6" width="8" height="6" fill="#2f5fa8"/><path d="M5 6l4 3.3L13 6" stroke="#fff" fill="none" stroke-width=".9"/></svg>
<div class="contact" style="top:668px">admin@meridianmobilelabs.com</div>
<svg class="contact-icon" style="top:698px" width="18" height="18" viewBox="0 0 18 18"><circle cx="9" cy="9" r="8" fill="none" stroke="#2f5fa8" stroke-width="1.2"/><circle cx="9" cy="9" r="4.5" fill="#2f5fa8"/><path d="M4.5 9h9M9 4.5c-2 2.5-2 6.5 0 9M9 4.5c2 2.5 2 6.5 0 9" stroke="#fff" fill="none" stroke-width=".7"/></svg>
<div class="contact" style="top:700px">www.meridianmobilelabs.com</div>
<svg class="contact-icon" style="top:731px" width="18" height="18" viewBox="0 0 18 18"><circle cx="9" cy="9" r="8" fill="none" stroke="#2f5fa8" stroke-width="1.2"/><path d="M9 14s-3.5-3.7-3.5-6.2a3.5 3.5 0 0 1 7 0C12.5 10.3 9 14 9 14z" fill="#2f5fa8"/><circle cx="9" cy="7.8" r="1.2" fill="#fff"/></svg>
<div class="contact" style="top:732px">1480 Cedar Ridge Drive<br><span style="display:inline-block;margin-top:2px">Suite 210, Riverton, Nevada 89000</span></div>

<div class="abs center headline" style="left:851px;top:632px;font-size:35px;line-height:40px;color:var(--ink);font-weight:600">50 Years</div>
<div class="abs center headline" style="left:851px;top:671px;font-size:35px;line-height:40px;color:var(--blue);font-weight:600">Of Experience</div>
<div class="abs center" style="left:863px;top:728px;font-family:'Jost',sans-serif;font-weight:500;font-size:18px;color:var(--ink);text-transform:uppercase">Laboratory and phlebotomy services</div>

<!-- Inside spread -->
<div class="board board--inside"></div>
<svg class="abs" style="left:0;top:1100px" width="1200" height="1000" viewBox="0 1100 1200 1000">
  <defs>
    <linearGradient id="insideBg" x1="0" y1="0" x2="0" y2="1">
      <stop offset="0" stop-color="#111823"/><stop offset="1" stop-color="#252e45"/>
    </linearGradient>
  </defs>
  <rect x="92" y="1183" width="984" height="681" fill="url(#insideBg)"/>
  <path d="M300 1183 C480 1200 540 1320 620 1380 C720 1450 880 1420 1076 1548 L1076 1183 Z" fill="#1d2539" opacity=".8"/>
  <path d="M380 1183 C500 1210 560 1340 640 1400 C740 1470 900 1450 1076 1548 L1076 1580 C900 1470 740 1500 630 1420 C560 1360 520 1230 380 1183Z" fill="#0e141f" opacity=".8"/>
  <polygon points="589,1864 1076,1864 1110,1875 1110,2077 1076,2088 621,2088" fill="#252e45"/>
  <line x1="584" y1="1183" x2="584" y2="1864" stroke="#8a8f9a" stroke-dasharray="5 4"/>
  <line x1="589" y1="1864" x2="1076" y2="1864" stroke="#8a8f9a" stroke-dasharray="5 4"/>
  <line x1="1076" y1="1864" x2="1076" y2="2088" stroke="#8a8f9a" stroke-dasharray="5 4"/>
  <rect x="726" y="1915" width="213" height="123" rx="8" fill="none" stroke="var(--blue-line)" stroke-width="1.2"/>
  <line x1="911" y1="1908" x2="946" y2="1940" stroke="var(--blue-line)"/>
  <line x1="718" y1="2012" x2="753" y2="2045" stroke="var(--blue-line)"/>
</svg>

<div class="brand-mark" style="left:334px;top:1410px">
  <div class="brand-mark__circle" style="width:116px;height:116px"></div>
  <div class="brand-mark__name">Meridian Mobile Labs</div>
</div>

<div class="abs center" style="left:337px;top:1521px;font-size:14.5px;font-weight:500;color:var(--blue)">Meridian Mobile Labs</div>
<p class="intro">Meridian Mobile Labs has a wide range of laboratory testing that covers the following disease states: Anemia, Bone/Skeleton, Cardiac, Diabetes, Drugs of Abuse, General Chemistry, Hepatic, Immunosuppressant Drugs, Infectious Disease, Inflammatory, Lipids, Microbiology, Mycology Nutritional Assessment, Oncology, Pancreatic, Parasitology, Prenatal, Renal, Reproductive Endocrinology, Respiratory, Sepsis, Spinal, Therapeutic Drug Monitoring, Metabolic, Toxicology, Urinalysis and Virology.</p>

<div class="services"></div>
<div class="service" style="left:150px;top:1641px"><svg width="16" height="16" viewBox="0 0 16 16"><path d="M13 7.5A5.5 5.5 0 1 1 10 2.6" fill="none" stroke="#fff" stroke-width="1.1"/><path d="M5 7.5l2.5 2.5L15 2.5" fill="none" stroke="#fff" stroke-width="1.1"/></svg>Clinical Chemistry</div>
<div class="service" style="left:291px;top:1641px"><svg width="16" height="16" viewBox="0 0 16 16"><path d="M13 7.5A5.5 5.5 0 1 1 10 2.6" fill="none" stroke="#fff" stroke-width="1.1"/><path d="M5 7.5l2.5 2.5L15 2.5" fill="none" stroke="#fff" stroke-width="1.1"/></svg>Parisitology</div>
<div class="service" style="left:401px;top:1641px"><svg width="16" height="16" viewBox="0 0 16 16"><path d="M13 7.5A5.5 5.5 0 1 1 10 2.6" fill="none" stroke="#fff" stroke-width="1.1"/><path d="M5 7.5l2.5 2.5L15 2.5" fill="none" stroke="#fff" stroke-width="1.1"/></svg>Immunohematology</div>
<div class="service" style="left:150px;top:1678px"><svg width="16" height="16" viewBox="0 0 16 16"><path d="M13 7.5A5.5 5.5 0 1 1 10 2.6" fill="none" stroke="#fff" stroke-width="1.1"/><path d="M5 7.5l2.5 2.5L15 2.5" fill="none" stroke="#fff" stroke-width="1.1"/></svg>Mycology</div>
<div class="service" style="left:291px;top:1678px"><svg width="16" height="16" viewBox="0 0 16 16"><path d="M13 7.5A5.5 5.5 0 1 1 10 2.6" fill="none" stroke="#fff" stroke-width="1.1"/><path d="M5 7.5l2.5 2.5L15 2.5" fill="none" stroke="#fff" stroke-width="1.1"/></svg>Urinalysis</div>
<div class="service" style="left:401px;top:1678px"><svg width="16" height="16" viewBox="0 0 16 16"><path d="M13 7.5A5.5 5.5 0 1 1 10 2.6" fill="none" stroke="#fff" stroke-width="1.1"/><path d="M5 7.5l2.5 2.5L15 2.5" fill="none" stroke="#fff" stroke-width="1.1"/></svg>Tumor Markers</div>
<div class="service" style="left:150px;top:1713px"><svg width="16" height="16" viewBox="0 0 16 16"><path d="M13 7.5A5.5 5.5 0 1 1 10 2.6" fill="none" stroke="#fff" stroke-width="1.1"/><path d="M5 7.5l2.5 2.5L15 2.5" fill="none" stroke="#fff" stroke-width="1.1"/></svg>Microbiology</div>
<div class="service" style="left:291px;top:1713px"><svg width="16" height="16" viewBox="0 0 16 16"><path d="M13 7.5A5.5 5.5 0 1 1 10 2.6" fill="none" stroke="#fff" stroke-width="1.1"/><path d="M5 7.5l2.5 2.5L15 2.5" fill="none" stroke="#fff" stroke-width="1.1"/></svg>Hematology</div>
<div class="service" style="left:401px;top:1713px"><svg width="16" height="16" viewBox="0 0 16 16"><path d="M13 7.5A5.5 5.5 0 1 1 10 2.6" fill="none" stroke="#fff" stroke-width="1.1"/><path d="M5 7.5l2.5 2.5L15 2.5" fill="none" stroke="#fff" stroke-width="1.1"/></svg>Virology</div>

</body>
</html>
```